UI/ UX Design for ERP Software

We need a new UX/UI interface for a ERP software for property managers. Our CMMS / ERP solution is made based on responsive design technologies and is coded in PHP.
The overall UX to be similar to Tev Ulna - easy navigation, intuitive menus.

Industry/Entity Type

Property Management

Number of Pages Required

5+ page

Requirements
Must have
• Round dock buttons
Consistent icons across the application
Enough Spacing between buttons/icons/ menu
Consistent Font
Nice to have
• We would like the UX to allow the users to use the application without /minimum training.
Should not have
• we don't want anything that is classic with respect to UX

```html
<!DOCTYPE html>
<html lang="en">
<head>
<meta charset="utf-8">
<title>Hestio – Active dashboard</title>
<link href="https://fonts.googleapis.com/css2?family=Roboto:wght@300;400;500;700&display=swap" rel="stylesheet">
<style>
:root{
  --brand:#0a7bff;
  --brand-dark:#0066e0;
  --accent:#1aa3ef;
  --bg:#e6f3fa;
  --white:#ffffff;
  --ink:#111418;
  --muted:#2a2f36;
  --grid:#9aa3ad;
  --bar:#7fb3e8;
  --sw-green:#93e67f;
  --sw-orange:#f7a35c;
  --sw-dark:#434348;
  --sw-violet:#8085e9;
  --sw-pink:#f15c80;
  --sw-yellow:#e4d354;
}
*{box-sizing:border-box;margin:0;padding:0}
html,body{width:1092px;height:1200px;overflow:hidden}
body{font-family:"Roboto",sans-serif;background:var(--bg);position:relative;color:var(--ink)}

/* sidebar */
.sidebar{position:absolute;left:0;top:0;width:193px;height:1200px;background:var(--brand);border-bottom-right-radius:10px}
.brand{height:55px;display:flex;align-items:center;justify-content:center;gap:8px;border-bottom:1px solid rgba(255,255,255,.15);color:var(--white);font-size:24px;font-weight:500}
.brand-dot{width:14px;height:14px;background:var(--white);border-radius:3px}
.nav-item{position:absolute;left:28px;width:165px;display:flex;align-items:flex-start;gap:10px;color:var(--white);font-size:15px;font-weight:300;line-height:22px}
.nav-item svg{flex:none;width:18px;height:18px;margin-top:2px}
.nav-item.active{left:18px;width:175px;height:39px;background:var(--white);color:var(--brand);border-radius:20px 0 0 20px;align-items:center;padding-left:7px;gap:9px}
.nav-item.active .nav-ic{width:27px;height:27px;border-radius:50%;background:var(--brand);display:flex;align-items:center;justify-content:center}
.nav-item.active svg{width:15px;height:15px;margin:0}

/* header */
.topbar{position:absolute;left:193px;top:0;width:899px;height:73px;background:var(--white)}
.hamburger{position:absolute;left:22px;top:25px;width:24px;height:18px;display:flex;flex-direction:column;justify-content:space-between}
.hamburger span{height:2px;background:var(--ink)}
.search{position:absolute;left:170px;top:18px;width:307px;height:35px;border:1px solid #8aa0b6;border-radius:2px;display:flex}
.search-input{flex:1;font-size:14px;color:#555;padding:9px 16px;font-weight:400}
.search-btn{width:48px;background:var(--accent);display:flex;align-items:center;justify-content:center}
.icon-badge{position:absolute;top:19px}
.badge{position:absolute;top:-6px;right:-6px;width:15px;height:15px;border-radius:50%;background:var(--accent);color:var(--white);font-size:10px;display:flex;align-items:center;justify-content:center}
.avatar{position:absolute;left:760px;top:11px;width:50px;height:50px;border-radius:50%;background:radial-gradient(circle at 50% 40%,#d7b79a,#8a6a52)}

.page-title{position:absolute;left:213px;top:104px;font-size:31px;font-weight:300;color:var(--accent)}

/* stat cards */
.stat{position:absolute;top:193px;height:189px;background:var(--white);text-align:center}
.stat-label{font-size:12px;font-weight:700;letter-spacing:.4px;margin-top:31px}
.stat-value{font-size:16px;font-weight:700;margin-top:14px;height:20px}
.stat svg{position:absolute;left:50%;transform:translateX(-50%);top:104px}
.stat.simple .stat-label{margin-top:50px}

/* period filters */
.period{position:absolute;top:418px;height:54px;background:var(--white);display:flex;align-items:center;justify-content:center;gap:5px;font-size:14px;color:var(--muted)}

/* chart */
.chart{position:absolute;left:218px;top:519px;width:852px;height:390px;background:var(--white);box-shadow:0 1px 4px rgba(0,0,0,.12)}
.chart-title{position:absolute;left:18px;top:18px;display:flex;align-items:center;gap:10px;font-size:14px}
.gridline{position:absolute;left:74px;width:742px;height:1px;background:var(--grid)}
.y-label{position:absolute;width:62px;text-align:right;font-size:13px;left:0}
.axis-y{position:absolute;left:74px;top:70px;width:1px;height:251px;background:var(--grid)}
.bar{position:absolute;left:363px;top:120px;width:55px;height:200px;background:var(--bar);border-radius:2px 2px 0 0}
.x-label{position:absolute;top:334px;font-size:12px;width:90px;text-align:center}

/* legend */
.legend{position:absolute;width:195px;height:71px;background:var(--white);box-shadow:0 1px 4px rgba(0,0,0,.12);display:flex;align-items:center;gap:14px;padding-left:14px;font-size:14px;font-weight:500;line-height:22px}
.swatch{flex:none;width:26px;height:30px}

.footer{position:absolute;top:1153px;left:193px;width:845px;text-align:center;font-size:14px;color:var(--muted)}
</style>
</head>
<body>

<aside class="sidebar">
  <div class="brand"><span class="brand-dot"></span>Hestio</div>

  <div class="nav-item active" style="top:72px"><span class="nav-ic"><svg viewBox="0 0 20 20" fill="#fff"><path d="M10 2 1 10h3v8h4v-5h4v5h4v-8h3z"/></svg></span>Dashboard</div>
  <div class="nav-item" style="top:125px"><svg viewBox="0 0 20 20" fill="#fff"><circle cx="10" cy="6" r="3"/><circle cx="4" cy="8" r="2.3"/><circle cx="16" cy="8" r="2.3"/><path d="M5 17a5 5 0 0 1 10 0zM0 17a4 4 0 0 1 5-4v4zM20 17a4 4 0 0 0-5-4v4z"/></svg>Customers</div>
  <div class="nav-item" style="top:168px"><svg viewBox="0 0 20 20" fill="#fff"><path d="M10 2 1 10h3v8h4v-5h4v5h4v-8h3z"/></svg>Properties</div>
  <div class="nav-item" style="top:211px"><svg viewBox="0 0 20 20" fill="none" stroke="#fff" stroke-width="2"><circle cx="10" cy="10" r="8"/><circle cx="10" cy="8" r="2.5" fill="#fff"/><path d="M5 15a6 6 0 0 1 10 0"/></svg>Tenants</div>
  <div class="nav-item" style="top:254px"><svg viewBox="0 0 20 20" fill="#fff"><circle cx="10" cy="6" r="4"/><path d="M3 18a7 7 0 0 1 14 0z"/></svg>Contacts</div>
  <div class="nav-item" style="top:297px"><svg viewBox="0 0 20 20" fill="#fff"><circle cx="7" cy="12" r="5"/><circle cx="15" cy="5" r="3.5"/><circle cx="7" cy="12" r="1.8" fill="var(--brand)"/></svg>Contractors</div>
  <div class="nav-item" style="top:341px"><svg viewBox="0 0 20 20" fill="#fff"><circle cx="10" cy="6" r="3"/><circle cx="4" cy="8" r="2.3"/><circle cx="16" cy="8" r="2.3"/><path d="M5 17a5 5 0 0 1 10 0zM0 17a4 4 0 0 1 5-4v4zM20 17a4 4 0 0 0-5-4v4z"/></svg>Employees</div>
  <div class="nav-item" style="top:384px"><svg viewBox="0 0 20 20" fill="none" stroke="#fff" stroke-width="1.6"><path d="M4 1h8l4 4v14H4z"/><path d="M7 13l3-4 3 4"/></svg>Compliance<br>Management</div>
  <div class="nav-item" style="top:450px"><svg viewBox="0 0 20 20" fill="#fff"><circle cx="7" cy="12" r="5"/><circle cx="15" cy="5" r="3.5"/><circle cx="7" cy="12" r="1.8" fill="var(--brand)"/></svg>Prevent.<br>Maintenance</div>
  <div class="nav-item" style="top:519px"><svg viewBox="0 0 20 20" fill="#fff"><circle cx="10" cy="10" r="7"/><circle cx="10" cy="10" r="2.5" fill="var(--brand)"/></svg>Work Orders</div>
  <div class="nav-item" style="top:562px"><svg viewBox="0 0 20 20" fill="none" stroke="#fff" stroke-width="2"><path d="M6 5 1 10l5 5M14 5l5 5-5 5M12 3 8 17"/></svg>Purchase Orders</div>
  <div class="nav-item" style="top:604px"><svg viewBox="0 0 20 20" fill="none" stroke="#fff" stroke-width="2.5"><circle cx="8" cy="8" r="5.5"/><path d="M12 12l6 6"/></svg>Property<br>Inspections</div>
  <div class="nav-item" style="top:675px"><svg viewBox="0 0 20 20" fill="#fff"><path d="M1 2h2v15h16v2H1z"/><rect x="5" y="9" width="2.5" height="6"/><rect x="9" y="5" width="2.5" height="10"/><rect x="13" y="8" width="2.5" height="7"/></svg>Energy<br>Management</div>
  <div class="nav-item" style="top:750px"><svg viewBox="0 0 20 20" fill="#fff"><path d="M10 1 19 18H1z"/><rect x="9" y="7" width="2" height="6" fill="var(--brand)"/><rect x="9" y="14" width="2" height="2" fill="var(--brand)"/></svg>Risk Management</div>
  <div class="nav-item" style="top:793px"><svg viewBox="0 0 20 20" fill="#fff"><rect x="1" y="3" width="18" height="14"/><path d="M3 6h14M3 9h14M3 12h14" stroke="var(--brand)" stroke-width="1.2"/></svg>Project<br>Management</div>
  <div class="nav-item" style="top:861px"><svg viewBox="0 0 20 20" fill="#fff"><rect x="1" y="4" width="18" height="12"/><circle cx="10" cy="10" r="3" fill="var(--brand)"/></svg>Financial<br>- Budgeting</div>
  <div class="nav-item" style="top:935px"><svg viewBox="0 0 20 20" fill="#fff"><ellipse cx="8" cy="8" rx="7" ry="5"/><ellipse cx="13" cy="12" rx="6" ry="4"/></svg>Tenant Requests</div>
  <div class="nav-item" style="top:978px"><svg viewBox="0 0 20 20" fill="#fff"><path d="M1 2h2v15h16v2H1z"/><rect x="5" y="9" width="2.5" height="6"/><rect x="9" y="5" width="2.5" height="10"/><rect x="13" y="8" width="2.5" height="7"/></svg>Visual Reports</div>
  <div class="nav-item" style="top:1022px"><svg viewBox="0 0 20 20" fill="#fff"><path d="M4 1h8l4 4v14H4z"/><path d="M7 10h6M7 13h6" stroke="var(--brand)" stroke-width="1.4"/></svg>Files</div>
  <div class="nav-item" style="top:1065px"><svg viewBox="0 0 20 20" fill="#fff"><path d="M4 1h8l4 4v14H4z"/><path d="M7 10h6M7 13h6" stroke="var(--brand)" stroke-width="1.4"/></svg>Pages</div>
  <div class="nav-item" style="top:1108px"><svg viewBox="0 0 20 20" fill="#fff"><circle cx="7" cy="12" r="5"/><circle cx="15" cy="5" r="3.5"/><circle cx="7" cy="12" r="1.8" fill="var(--brand)"/></svg>Configurations</div>
  <div class="nav-item" style="top:1151px"><svg viewBox="0 0 20 20" fill="#fff"><path d="M2 16 11 7a4 4 0 1 1 2 2l-9 9z"/></svg>Settings</div>
</aside>

<header class="topbar">
  <div class="hamburger"><span></span><span></span><span></span></div>
  <div class="search">
    <div class="search-input">Search</div>
    <div class="search-btn"><svg width="14" height="14" viewBox="0 0 20 20" fill="none" stroke="#fff" stroke-width="3"><circle cx="8" cy="8" r="5.5"/><path d="M12 12l6 6"/></svg></div>
  </div>
  <div class="icon-badge" style="left:650px"><svg width="24" height="26" viewBox="0 0 24 26" fill="none" stroke="#111" stroke-width="1.6"><path d="M5 18V11a7 7 0 0 1 14 0v7l2 2H3z"/><path d="M10 22a2 2 0 0 0 4 0"/></svg><span class="badge">6</span></div>
  <div class="icon-badge" style="left:702px"><svg width="26" height="26" viewBox="0 0 26 26" fill="none" stroke="#111" stroke-width="1.6"><path d="M2 4h22v14H10l-6 5v-5H2z"/><path d="M6 9h14M6 13h14"/></svg><span class="badge">6</span></div>
  <div class="avatar" role="img" aria-label="User profile photo"></div>
</header>

<h1 class="page-title">Active dashboard</h1>

<div class="stat simple" style="left:214px;width:135px">
  <div class="stat-label">PROPERTIES</div>
  <svg width="66" height="54" viewBox="0 0 66 54" fill="var(--brand)"><path d="M33 2 1 28l4 5 28-23 28 23 4-5z"/><path d="M10 30 33 12l23 18v24H40V38H26v16H10z"/></svg>
</div>
<div class="stat simple" style="left:368px;width:140px">
  <div class="stat-label">TENANTS</div>
  <svg width="60" height="52" viewBox="0 0 60 52" fill="var(--brand)"><circle cx="30" cy="10" r="10"/><circle cx="10" cy="18" r="7"/><circle cx="50" cy="18" r="7"/><path d="M17 52V34a8 8 0 0 1 8-8h10a8 8 0 0 1 8 8v18z"/><path d="M0 52V36a6 6 0 0 1 6-6h8v22zM60 52V36a6 6 0 0 0-6-6h-8v22z"/></svg>
</div>
<div class="stat" style="left:526px;width:168px">
  <div class="stat-label">TOTAL PROPERTIES AREA</div>
  <div class="stat-value">$422,000.00 SQ.FT.</div>
  <svg width="56" height="56" viewBox="0 0 56 56" fill="var(--brand)"><path d="M28 0 38 11H32V24H45V18l11 10-11 10v-6H32v13h6L28 56 18 45h6V32H11v6L0 28l11-10v6h13V11h-6z"/></svg>
</div>
<div class="stat" style="left:714px;width:169px">
  <div class="stat-label">RENTED AREA</div>
  <div class="stat-value">$233,500.00 SQ.FT</div>
  <svg width="56" height="56" viewBox="0 0 56 56" fill="var(--brand)"><path d="M28 0 38 11H32V24H45V18l11 10-11 10v-6H32v13h6L28 56 18 45h6V32H11v6L0 28l11-10v6h13V11h-6z"/></svg>
</div>
<div class="stat" style="left:903px;width:169px">
  <div class="stat-label">VACANCIES AREA</div>
  <div class="stat-value">$188,500.00</div>
  <svg width="56" height="56" viewBox="0 0 56 56" fill="var(--brand)"><path d="M28 0 38 11H32V24H45V18l11 10-11 10v-6H32v13h6L28 56 18 45h6V32H11v6L0 28l11-10v6h13V11h-6z"/></svg>
</div>

<div class="period" style="left:213px;width:127px"><svg width="13" height="13" viewBox="0 0 14 14" fill="none" stroke="var(--brand)" stroke-width="1.6"><circle cx="7" cy="7" r="6"/><path d="M7 3.5V7H4.5"/></svg>LAST 7 DAYS</div>
<div class="period" style="left:356px;width:127px"><svg width="13" height="13" viewBox="0 0 14 14" fill="none" stroke="var(--brand)" stroke-width="1.6"><circle cx="7" cy="7" r="6"/><path d="M7 3.5V7H4.5"/></svg>LAST MONTHS</div>
<div class="period" style="left:492px;width:142px"><svg width="13" height="13" viewBox="0 0 14 14" fill="none" stroke="var(--brand)" stroke-width="1.6"><circle cx="7" cy="7" r="6"/><path d="M7 3.5V7H4.5"/></svg>LAST 3 MONTHS</div>
<div class="period" style="left:643px;width:128px"><svg width="13" height="13" viewBox="0 0 14 14" fill="none" stroke="var(--brand)" stroke-width="1.6"><circle cx="7" cy="7" r="6"/><path d="M7 3.5V7H4.5"/></svg>NEXT 7 DAYS</div>
<div class="period" style="left:788px;width:127px"><svg width="13" height="13" viewBox="0 0 14 14" fill="none" stroke="var(--brand)" stroke-width="1.6"><circle cx="7" cy="7" r="6"/><path d="M7 3.5V7H4.5"/></svg>NEXT MONTHS</div>
<div class="period" style="left:927px;width:137px"><svg width="13" height="13" viewBox="0 0 14 14" fill="none" stroke="var(--brand)" stroke-width="1.6"><circle cx="7" cy="7" r="6"/><path d="M7 3.5V7H4.5"/></svg>NEXT 3 MONTHS</div>

<section class="chart">
  <div class="chart-title"><svg width="20" height="20" viewBox="0 0 20 20" fill="#111"><rect x="0" y="8" width="4" height="12"/><rect x="7" y="0" width="5" height="20"/><rect x="15" y="5" width="5" height="15"/></svg>12/27/2021 - 01/03/2021</div>

  <div class="gridline" style="top:70px"></div>
  <div class="gridline" style="top:120px"></div>
  <div class="gridline" style="top:170px"></div>
  <div class="gridline" style="top:220px"></div>
  <div class="gridline" style="top:270px"></div>
  <div class="gridline" style="top:320px"></div>
  <div class="axis-y"></div>

  <div class="y-label" style="top:61px">1.25</div>
  <div class="y-label" style="top:111px">1</div>
  <div class="y-label" style="top:161px">0.75</div>
  <div class="y-label" style="top:211px">0.5</div>
  <div class="y-label" style="top:261px">0.25</div>
  <div class="y-label" style="top:311px">0</div>

  <div class="bar"></div>

  <div class="x-label" style="left:66px">12/27/2021</div>
  <div class="x-label" style="left:161px">12/28/2021</div>
  <div class="x-label" style="left:257px">12/29/2021</div>
  <div class="x-label" style="left:352px">12/30/2021</div>
  <div class="x-label" style="left:448px">12/31/2021</div>
  <div class="x-label" style="left:546px">12/01/20201</div>
  <div class="x-label" style="left:639px">12/02/2021</div>
  <div class="x-label" style="left:735px">12/03/2021</div>
</section>

<div class="legend" style="left:222px;top:955px"><span class="swatch" style="background:var(--bar)"></span>Scheduled<br>Maintenance</div>
<div class="legend" style="left:438px;top:955px;gap:8px;padding-left:6px"><span class="swatch" style="background:var(--sw-green)"></span>Completed Scheduled<br>Maintenance</div>
<div class="legend" style="left:654px;top:955px"><span class="swatch" style="background:var(--sw-orange)"></span>Future Scheduled<br>Maintenance</div>
<div class="legend" style="left:870px;top:955px;gap:16px"><span class="swatch" style="background:var(--sw-dark)"></span>Scheduled Work<br>Orders</div>
<div class="legend" style="left:222px;top:1046px;gap:10px"><span class="swatch" style="background:var(--sw-violet)"></span>Completed Work<br>Orders</div>
<div class="legend" style="left:438px;top:1046px"><span class="swatch" style="background:var(--sw-pink)"></span>Property Inspections<br>in Progress</div>
<div class="legend" style="left:653px;top:1046px"><span class="swatch" style="background:var(--sw-yellow)"></span>Completed Property<br>Inspections</div>

<footer class="footer">© 2021 ERP SOFTWARE ALL RIGHTS RESERVED</footer>

</body>
</html>
```